New iOS App design for Boston Startup

We are looking for a new app design for our iPhone app. The current app's design feels outdated and we like to add lots of new functionality and a new navigation as well. A complete overhaul therefore!
We want you to design 5 screens that will have changed the most. The complete wireframes of these 5 pages are attached in the requirements document.
Once the winning design is selected we will award the winner with the designing all other screens (40-50 screens based on the same design). This will be a separate project worth $1000. The winning designer can get more follow up work if both sides are happy about the cooperation.
We will give feedback as soon as the first screen has been uploaded for review. Final decision will be made only after all 5 screens are finished.
We hope you give it your best!
Note: will only communicate through PixelHarbor (no skype),
Updates
Reason: Want to give designers a chance to submit their designs as I understand from some, the deadline is too close.
I have raised the award and introduced a 2nd price as well to make it worth your time. I hope you give it your best shot.
Reason: A few of you have asked for an extension of the deadline as time is running out. I will extend by one day. Tell me if you need more.
Industry/Entity Type
Startup
Requirements
Must have
- At least 1 screen before we can give you feedback.
Nice to have
- multiple options of 1 screen to get to a desirable design

```html
<!DOCTYPE html>
<html lang="en">
<head>
<meta charset="utf-8">
<title>Study Dashboard – Home Screen</title>
<link rel="stylesheet" href="https://fonts.googleapis.com/css2?family=Roboto:wght@300;400;500;700&display=swap">
<style>
  :root {
    --page-bg: #eef0f3;
    --screen-bg: #ffffff;
    --blue: #1f86d4;
    --blue-light: #3fb3e8;
    --blue-tile: #2189d6;
    --text-dark: #333a40;
    --text-mid: #5d6368;
    --text-soft: #8a9096;
    --stat-bg: #f5f5f5;
    --panel-bg: #efefef;
    --divider: #dcdcdc;
    --plus-green: #4f9a1e;
    --minus-red: #e8322b;
    --button-grey: #666a6e;
    --tab-grey: #6b7075;
  }
  * { box-sizing: border-box; margin: 0; padding: 0; }
  html, body {
    width: 1200px; height: 799px; overflow: hidden;
    background: var(--page-bg);
    font-family: "Roboto", "Helvetica Neue", Arial, sans-serif;
  }
  .screen {
    position: absolute; left: 390px; top: 26px;
    width: 420px; height: 747px;
    background: var(--screen-bg);
    border-radius: 6px; overflow: hidden;
    box-shadow: 0 10px 30px rgba(30,50,80,.15);
    display: flex; flex-direction: column;
  }
  .top-bar {
    background: linear-gradient(90deg, var(--blue-light) 0%, var(--blue) 55%);
    color: #fff;
  }
  .status-bar {
    height: 22px; display: flex; align-items: center; justify-content: space-between;
    padding: 0 10px; font-size: 11px; font-weight: 500;
  }
  .status-left, .status-right { display: flex; align-items: center; gap: 5px; width: 120px; }
  .status-right { justify-content: flex-end; }
  .header {
    height: 54px; display: flex; align-items: center; position: relative;
  }
  .menu-button { position: absolute; left: 16px; top: 16px; }
  .header-title { width: 100%; text-align: center; font-size: 21px; font-weight: 700; letter-spacing: .2px; }

  .score-row {
    height: 92px; display: flex; align-items: center; justify-content: center; gap: 12px;
    position: relative;
  }
  .score-label { font-size: 36px; font-weight: 300; color: var(--text-mid); }
  .score-value { font-size: 72px; font-weight: 700; color: var(--blue); letter-spacing: -2px; }
  .score-delta { font-size: 26px; color: var(--minus-red); align-self: flex-start; margin-top: 12px; margin-left: -8px; }
  .scroll-hint { position: absolute; font-size: 13px; color: var(--text-soft); }

  .stats-row {
    height: 70px; background: var(--stat-bg); display: flex;
    border-top: 1px solid var(--divider); border-bottom: 1px solid var(--divider);
    position: relative;
  }
  .stat {
    flex: 1; display: flex; flex-direction: column; justify-content: center; align-items: center;
    border-right: 1px solid var(--divider); font-size: 14px; color: var(--text-mid);
  }
  .stat:last-child { border-right: none; }
  .stat-figure { font-size: 15px; color: var(--text-dark); }
  .stat-figure b { color: var(--plus-green); font-weight: 500; }
  .stat-week { justify-content: flex-start; padding-top: 10px; }

  .tiles { display: flex; gap: 4px; padding: 4px 0; background: #fff; }
  .tile {
    flex: 1; height: 130px; background: var(--blue-tile); color: #fff;
    display: flex; flex-direction: column; align-items: center; justify-content: center;
    gap: 8px; position: relative; font-size: 15px; text-align: center; line-height: 1.2;
  }
  .tile-chevron { position: absolute; right: 12px; top: 12px; }

  .up-next {
    flex: 1; background: var(--panel-bg);
    display: flex; flex-direction: column; align-items: center; justify-content: center; gap: 18px;
  }
  .up-next-label { font-size: 27px; color: var(--text-dark); font-weight: 400; }
  .up-next-button {
    width: 360px; height: 52px; border-radius: 6px; background: var(--button-grey);
    color: #fff; font-size: 21px; font-weight: 300; display: flex; align-items: center; justify-content: center;
  }

  .tab-bar {
    height: 64px; display: flex; border-top: 1px solid var(--divider); background: #fff;
  }
  .tab {
    flex: 1; display: flex; flex-direction: column; align-items: center; justify-content: center; gap: 3px;
    font-size: 12px; color: var(--text-dark);
  }
  .tab svg { stroke: var(--tab-grey); fill: none; stroke-width: 1.6; }
  .tab.is-active { color: var(--blue); }
</style>
</head>
<body>
<main class="screen">
  <header class="top-bar">
    <div class="status-bar">
      <div class="status-left">
        <span>●●●</span><span>ZEPHRO</span>
        <svg width="13" height="10" viewBox="0 0 13 10" fill="none" stroke="#fff" stroke-width="1.4"><path d="M1 3.5a8 8 0 0 1 11 0M3 5.8a5 5 0 0 1 7 0"/><circle cx="6.5" cy="8.4" r="1" fill="#fff"/></svg>
      </div>
      <span class="status-time">4:21 PM</span>
      <div class="status-right">
        <svg width="7" height="11" viewBox="0 0 7 11" fill="none" stroke="#fff" stroke-width="1.2"><path d="M1 3l5 5-2.5 2V1L6 3 1 8"/></svg>
        <span>100%</span>
        <svg width="22" height="10" viewBox="0 0 22 10"><rect x=".5" y=".5" width="19" height="9" rx="2" fill="none" stroke="#fff"/><rect x="2" y="2" width="16" height="6" rx="1" fill="#fff"/><rect x="20" y="3" width="1.5" height="4" fill="#fff"/></svg>
      </div>
    </div>
    <div class="header">
      <svg class="menu-button" width="24" height="20" viewBox="0 0 24 20" stroke="#fff" stroke-width="3" stroke-linecap="round"><path d="M2 2h20M2 10h20M2 18h20"/></svg>
      <h1 class="header-title">Welcome back, Aren</h1>
    </div>
  </header>

  <section class="score-row">
    <span class="scroll-hint" style="right:12px;top:6px">›</span>
    <span class="score-label">Score</span>
    <span class="score-value">650</span>
    <span class="score-delta">-18</span>
  </section>

  <section class="stats-row">
    <div class="stat"><span class="stat-figure"><b>34%</b> +4</span><span>Completion</span></div>
    <div class="stat"><span class="stat-figure"><b>20</b> +3</span><span>Sessions</span></div>
    <div class="stat"><span class="stat-figure"><b>18</b> +10</span><span>Sessions</span></div>
    <div class="stat stat-week"><span>This week</span></div>
  </section>

  <section class="tiles">
    <div class="tile">
      <svg class="tile-chevron" width="8" height="12" viewBox="0 0 8 12" fill="none" stroke="#fff" stroke-width="2"><path d="M1 1l5 5-5 5"/></svg>
      <svg width="38" height="30" viewBox="0 0 38 30" fill="none" stroke="#fff" stroke-width="1.5"><path d="M3 28V18M9 28V14M15 28V16M21 28V10M27 28V12M33 28V6"/><path d="M2 16l8-6 6 3 7-8 6 4 7-7"/></svg>
      <span>Analytics</span>
    </div>
    <div class="tile">
      <svg class="tile-chevron" width="8" height="12" viewBox="0 0 8 12" fill="none" stroke="#fff" stroke-width="2"><path d="M1 1l5 5-5 5"/></svg>
      <svg width="38" height="28" viewBox="0 0 38 28" fill="none" stroke="#fff" stroke-width="1.5"><path d="M19 5C14 2 7 2 2 4v20c5-2 12-2 17 1 5-3 12-3 17-1V4c-5-2-12-2-17 1zM19 5v20"/></svg>
      <span>Course<br>Overview</span>
    </div>
    <div class="tile">
      <svg class="tile-chevron" width="8" height="12" viewBox="0 0 8 12" fill="none" stroke="#fff" stroke-width="2"><path d="M1 1l5 5-5 5"/></svg>
      <svg width="38" height="32" viewBox="0 0 38 32" fill="none" stroke="#fff" stroke-width="1.5"><rect x="2" y="5" width="28" height="24" rx="2"/><path d="M2 11h28M9 2v6M23 2v6M8 16h4M14 16h4M8 21h4M14 21h4"/><circle cx="29" cy="22" r="7" fill="#2189d6"/><path d="M29 18v4l3 2"/></svg>
      <span>Days Until<br>Test 33</span>
    </div>
  </section>

  <section class="up-next">
    <h2 class="up-next-label">Up Next:</h2>
    <div class="up-next-button">Sentence Correction Lesson 4</div>
  </section>

  <nav class="tab-bar">
    <div class="tab">
      <svg width="26" height="24" viewBox="0 0 26 24"><path d="M2 12L13 2l11 10M5 10v12h6v-7h4v7h6V10"/></svg>
      <span>Home</span>
    </div>
    <div class="tab">
      <svg width="30" height="24" viewBox="0 0 30 24"><path d="M15 4C11 2 6 2 2 3v18c4-1 9-1 13 1 4-2 9-2 13-1V3c-4-1-9-1-13 1zM15 4v18"/></svg>
      <span>Theory</span>
    </div>
    <div class="tab is-active">
      <svg width="26" height="26" viewBox="0 0 26 26" style="stroke:none;fill:var(--blue)"><path d="M13 1l11 5-11 5L2 6z"/><path d="M2 11l11 5 11-5v3l-11 5-11-5z"/><path d="M2 18l11 5 11-5v3l-11 5-11-5z"/></svg>
      <span>Practice</span>
    </div>
    <div class="tab">
      <svg width="34" height="22" viewBox="0 0 34 22"><path d="M9 3h16c5 0 8 6 8 13 0 4-3 5-6 2l-3-3H10l-3 3c-3 3-6 2-6-2C1 9 4 3 9 3z"/><path d="M9 7v6M6 10h6"/><circle cx="23" cy="8" r="1.2"/><circle cx="26" cy="11" r="1.2"/></svg>
      <span>Games</span>
    </div>
    <div class="tab">
      <svg width="30" height="24" viewBox="0 0 30 24"><path d="M8 21a6 6 0 0 1-1-12 8 8 0 0 1 15-2 7 7 0 0 1 1 14z"/><path d="M10 13l4 4 7-8"/></svg>
      <span>Test</span>
    </div>
  </nav>
</main>
</body>
</html>
```